Tolbek cards

I want a simple business card that pops.
Logo on one side.
On side two i want.
"Are you thinking about a new building on your property, or renovating an existing structure? Contact".....
Owners Name: Dale Whitacre
Owners Phone number: 610-555-0187
Address:4076 Copper Ridge RD, Marlow Springs, OH 44019
Committed to Quality, Service, and Integrity

```html
<!DOCTYPE html>
<html lang="en">
<head>
<meta charset="utf-8">
<title>Tolbek Builders LLC – Business Cards</title>
<link rel="stylesheet" href="https://fonts.googleapis.com/css2?family=Archivo+Black&family=Arimo:wght@400;700&family=Patrick+Hand&display=swap">
<style>
  :root {
    --backdrop: #262626;
    --brown-light: #a08a6e;
    --brown-dark: #5a4030;
    --brown-ink: #4a3527;
    --brown-mid: #8e7558;
    --paper: #f1f0ee;
    --white: #f4f2ef;
    --text-dark: #3a2c22;
  }
  html, body { margin: 0; padding: 0; overflow: hidden; }
  body {
    width: 1200px; height: 576px;
    background: var(--backdrop);
    position: relative;
    font-family: "Arimo", Arial, sans-serif;
  }
  .card {
    position: absolute; top: 139px;
    width: 484px; height: 293px;
    border-radius: 10px; overflow: hidden;
  }
  .card--front {
    left: 102px;
    background: linear-gradient(180deg, var(--brown-light) 0%, var(--brown-dark) 100%);
  }
  .card--back { left: 596px; background: var(--paper); }

  /* front */
  .front-brand {
    position: absolute; left: 0; right: 0; top: 58px;
    text-align: center; color: var(--white);
  }
  .brand-square {
    width: 56px; height: 56px; margin: 0 auto 12px;
    background: var(--white); opacity: .9;
  }
  .front-brand .brand-name {
    font-family: "Archivo Black", Arial, sans-serif;
    font-size: 46px; line-height: 1; letter-spacing: 1px;
  }
  .front-brand .brand-sub {
    font-family: "Arimo", Arial, sans-serif; font-weight: 700;
    font-size: 16px; letter-spacing: 2px; margin-top: 4px;
  }
  .front-tagline {
    position: absolute; left: 0; right: 0; top: 257px;
    display: flex; align-items: center; justify-content: center; gap: 14px;
    color: var(--white); font-size: 13px;
  }
  .front-tagline .rule { width: 68px; height: 1px; background: var(--white); opacity: .8; }

  /* back */
  .back-brand {
    position: absolute; left: 20px; top: 24px;
    display: flex; align-items: center; gap: 12px; color: var(--brown-ink);
  }
  .back-brand .brand-square { width: 38px; height: 38px; margin: 0; background: var(--brown-ink); opacity: 1; }
  .back-brand .brand-name {
    font-family: "Archivo Black", Arial, sans-serif;
    font-size: 28px; line-height: 1; letter-spacing: 1px;
  }
  .back-brand .brand-sub { font-weight: 700; font-size: 10.5px; letter-spacing: 2.6px; margin-top: 2px; }
  .pitch {
    position: absolute; left: 20px; top: 86px; width: 200px; margin: 0;
    font-family: "Patrick Hand", cursive;
    font-size: 15.5px; line-height: 18px; color: var(--text-dark);
  }
  .contact-label {
    position: absolute; left: 20px; top: 150px; width: 206px;
    display: flex; align-items: center; gap: 6px;
    font-size: 9px; color: var(--text-dark);
  }
  .contact-label .rule { flex: 1; height: 1px; background: var(--brown-mid); }
  .owner {
    position: absolute; left: 20px; top: 168px; margin: 0;
    font-weight: 700; font-size: 19px; color: var(--text-dark);
  }
  .owner .surname { color: var(--brown-mid); }
  .details {
    position: absolute; left: 20px; top: 196px; margin: 0; padding: 0; list-style: none;
    font-size: 12.5px; line-height: 15px; color: var(--text-dark);
  }
  .details li { display: flex; gap: 6px; margin-bottom: 5px; }
  .details svg { flex: none; margin-top: 2px; }
  .back-tagline {
    position: absolute; left: 20px; top: 262px; font-size: 11px; color: var(--text-dark);
  }
  .brand-panel {
    position: absolute; right: 0; top: 0; width: 240px; height: 100%;
    background: linear-gradient(135deg, var(--brown-light), var(--brown-dark));
  }
</style>
</head>
<body>
  <section class="card card--front" aria-label="Card front">
    <div class="front-brand">
      <div class="brand-square"></div>
      <div class="brand-name">TOLBEK</div>
      <div class="brand-sub">BUILDERS LLC</div>
    </div>
    <div class="front-tagline">
      <span class="rule"></span>
      <span>Committed to Quality, Service &amp; Integrity</span>
      <span class="rule"></span>
    </div>
  </section>

  <section class="card card--back" aria-label="Card back">
    <div class="back-brand">
      <div class="brand-square"></div>
      <div>
        <div class="brand-name">TOLBEK</div>
        <div class="brand-sub">BUILDERS LLC</div>
      </div>
    </div>
    <p class="pitch">Are you thinking about a new building on your property, or renovating an existing structure?</p>
    <div class="contact-label"><span>Contact:</span><span class="rule"></span></div>
    <p class="owner">DALE <span class="surname">WHITACRE</span></p>
    <ul class="details">
      <li>
        <svg width="11" height="11" viewBox="0 0 24 24" fill="none" stroke="#6b5646" stroke-width="2"><circle cx="12" cy="12" r="10"/><path d="M8 7l2 0 1 3-1.5 1a7 7 0 0 0 3.5 3.5l1-1.5 3 1v2a1 1 0 0 1-1 1A10 10 0 0 1 7 8a1 1 0 0 1 1-1z"/></svg>
        <span>610-555-0187</span>
      </li>
      <li>
        <svg width="11" height="12" viewBox="0 0 24 26" fill="none" stroke="#6b5646" stroke-width="2"><path d="M12 24s-8-8-8-14a8 8 0 0 1 16 0c0 6-8 14-8 14z"/><circle cx="12" cy="10" r="3"/></svg>
        <span>4076 Copper Ridge RD,<br>Marlow Springs, OH 44019</span>
      </li>
    </ul>
    <div class="back-tagline">Committed to Quality, Service &amp; Integrity</div>
    <div class="brand-panel" role="img" aria-label="Large brand mark decoration in brown tones"></div>
  </section>
</body>
</html>
```